Gestaltung Mini Katalog für bayerische Polomarke
Gestaltung "Mini" Katalog für bayerische Polomarke
Zielgruppe
Unsere Marke richtet sich an den klassischen Lifestyle Kunden. 20 - 45 Jahre alt, legt Wert auf das Äussere und Kleidung.... Mag es gerne besonders, modern und chic.
Hallo,
wir planen derzeit einen kleinen Katalog von 8-10 Seiten im Format DIN A5 (kein Muss). Präsentiert wird darin die erste bayerische Polomarke K&M reitmode und die aktuellen Kollektionen an Polo-Teamshirts.
Die Fotos dazu werden in den nächsten 14 Tagen entstehen.
Wir suchen nun jemanden, der uns das ganze in eine moderne Gestaltung bringt. Für Vorschläge bitte statt der Fotos alternative Fotos einsetzen.
Unsere Marke bewegt sich im mittleren Preissegment und präsentiert eine ganz besondere Sportart. All das muss in dem Katalog rüber kommen. Neben den Produkt- und Modefotos werden klassische Polobilder integriert, um das Gefühl diesen Sports mit zu vermitteln.
Die Grundfarben sollten sich an denen von K&M reitmode orientieren: schwarz, blau, weiss.... Wobei wir für andere Farben, wenn diese passen bzw. begründet sind auch interessiert sind.

```html
<!DOCTYPE html>
<html lang="de">
<head>
<meta charset="utf-8">
<title>K&amp;M reitmode – Frauen-Poloshirts</title>
<link rel="stylesheet" href="https://fonts.googleapis.com/css2?family=Questrial&family=Arimo:wght@400;700&display=swap">
<style>
  :root {
    --night: #07090d;
    --night-glow: #1b2a3a;
    --ring: #22374c;
    --accent: #3aa2de;
    --band: #4aa6da;
    --band-light: #6cbbe6;
    --white: #ffffff;
    --text: #e9edf2;
    --shirt-dark: #101215;
    --shirt-mid: #2a2d33;
    --gap: #d9dde2;
  }
  * { margin: 0; padding: 0; box-sizing: border-box; }
  html, body { width: 1200px; height: 600px; overflow: hidden; background: var(--gap); }
  .spread { position: relative; width: 1200px; height: 600px; display: flex; gap: 6px; }
  .page {
    position: relative; width: 597px; height: 600px; overflow: hidden;
    background: var(--night);
  }
  .page-backdrop { position: absolute; inset: 0; width: 100%; height: 100%; }
  .band {
    position: absolute; left: 0; right: 0; top: 477px; bottom: 0;
    background: linear-gradient(180deg, var(--band-light), var(--band) 40%);
  }
  .product { position: absolute; top: 0; width: 270px; height: 600px; }
  .product-title {
    position: absolute; top: 58px; left: 0;
    font-family: "Questrial", sans-serif; font-size: 19px; letter-spacing: 0.2px;
    color: var(--white); font-weight: 400; white-space: nowrap;
  }
  .product-title .accent { color: var(--accent); }
  .product-copy {
    position: absolute; top: 92px; left: 0; width: 160px;
    font-family: "Arimo", sans-serif; font-size: 11px; line-height: 15.5px; color: var(--text);
  }
  .product-copy p + p { margin-top: 15px; }
  .order-number {
    position: absolute; top: 268px; left: 0;
    font-family: "Arimo", sans-serif; font-size: 11.5px; color: var(--text); white-space: nowrap;
  }
  .order-number span { color: var(--accent); }
  .shirt-image {
    position: absolute; top: 290px; left: -24px; width: 222px; height: 290px;
    border-radius: 60px 60px 30px 30px / 40px 40px 20px 20px;
    background: radial-gradient(ellipse at 50% 35%, var(--shirt-mid), var(--shirt-dark) 70%);
    box-shadow: 0 6px 18px rgba(0,0,0,0.35);
  }
  .price {
    position: absolute; top: 500px; left: 120px;
    font-family: "Arimo", sans-serif; font-weight: 700; font-size: 46px;
    color: var(--white); white-space: nowrap;
    text-shadow: 0 2px 6px rgba(0,0,0,0.55);
  }
</style>
</head>
<body>
<main class="spread">
  <section class="page page-left">
    <svg class="page-backdrop" viewBox="0 0 597 600" aria-hidden="true">
      <defs>
        <radialGradient id="glow-left" cx="0.45" cy="0.2" r="0.6">
          <stop offset="0" stop-color="#1e3042"/>
          <stop offset="1" stop-color="#07090d"/>
        </radialGradient>
      </defs>
      <rect width="597" height="600" fill="#07090d"/>
      <circle cx="340" cy="150" r="330" fill="url(#glow-left)"/>
      <circle cx="340" cy="150" r="330" fill="none" stroke="#2a4258" stroke-width="2" opacity="0.5"/>
      <circle cx="120" cy="-60" r="230" fill="#0a0e14" opacity="0.85"/>
      <circle cx="560" cy="560" r="260" fill="none" stroke="#1c2c3c" stroke-width="40" opacity="0.5"/>
    </svg>
    <div class="band"></div>

    <article class="product" style="left:72px">
      <h2 class="product-title">FRAUEN-<span class="accent">POLOSHIRT</span></h2>
      <div class="product-copy">
        <p>Das Shirt von K&amp;M reitmode in schwarz mit gedrucktem Logo. Tailliertes Girl-Shirt, hochwertiges Shirt aus 100% gekämmter Baumwolle, 240 g/m² , figurbetont.</p>
        <p>Bitte wählen Sie Ihre Größe: Größe S - Größe M - Größe L - Größe XL</p>
      </div>
      <p class="order-number">Bestellnummer : <span>111 - 234567</span></p>
      <div class="shirt-image" role="img" aria-label="Produktfoto: schwarzes taillierte Damen-Shirt mit blauem Polospieler-Motiv"></div>
      <p class="price">25 €</p>
    </article>

    <article class="product" style="left:342px">
      <h2 class="product-title">FRAUEN-<span class="accent">POLOSHIRT</span></h2>
      <div class="product-copy">
        <p>Das Shirt von K&amp;M reitmode in schwarz mit gedrucktem Logo. Tailliertes Girl-Shirt, hochwertiges Shirt aus 100% gekämmter Baumwolle, 240 g/m² , figurbetont.</p>
        <p>Bitte wählen Sie Ihre Größe: Größe S - Größe M - Größe L - Größe XL</p>
      </div>
      <p class="order-number">Bestellnummer : <span>111 - 234567</span></p>
      <div class="shirt-image" role="img" aria-label="Produktfoto: schwarzes Damen-Shirt mit weißem Polospieler-Motiv in Umrisslinien und Teamschriftzug"></div>
      <p class="price">25 €</p>
    </article>
  </section>

  <section class="page page-right">
    <svg class="page-backdrop" viewBox="0 0 597 600" aria-hidden="true">
      <defs>
        <radialGradient id="glow-right" cx="0.5" cy="0.3" r="0.6">
          <stop offset="0" stop-color="#1e3042"/>
          <stop offset="1" stop-color="#07090d"/>
        </radialGradient>
      </defs>
      <rect width="597" height="600" fill="#07090d"/>
      <circle cx="120" cy="60" r="300" fill="url(#glow-right)"/>
      <circle cx="120" cy="60" r="300" fill="none" stroke="#2a4258" stroke-width="2" opacity="0.5"/>
      <circle cx="470" cy="330" r="260" fill="#1a2b3c" opacity="0.7"/>
      <circle cx="470" cy="330" r="260" fill="none" stroke="#2d4860" stroke-width="2" opacity="0.6"/>
      <circle cx="560" cy="-40" r="170" fill="#0a0e14" opacity="0.9"/>
    </svg>
    <div class="band"></div>

    <article class="product" style="left:75px">
      <h2 class="product-title">FRAUEN-<span class="accent">POLOSHIRT</span></h2>
      <div class="product-copy">
        <p>Das Shirt von K&amp;M reitmode in schwarz mit gedrucktem Logo. Tailliertes Girl-Shirt, hochwertiges Shirt aus 100% gekämmter Baumwolle, 240 g/m² , figurbetont.</p>
        <p>Bitte wählen Sie Ihre Größe: Größe S - Größe M - Größe L - Größe XL</p>
      </div>
      <p class="order-number">Bestellnummer : <span>111 - 234567</span></p>
      <div class="shirt-image" role="img" aria-label="Produktfoto: schwarzes Damen-Shirt mit weißem Polospieler-Motiv und großer blauer Rückennummer 2"></div>
      <p class="price">25 €</p>
    </article>

    <article class="product" style="left:342px">
      <h2 class="product-title">FRAUEN-<span class="accent">POLOSHIRT</span></h2>
      <div class="product-copy">
        <p>Das Shirt von K&amp;M reitmode in schwarz mit gedrucktem Logo. Tailliertes Girl-Shirt, hochwertiges Shirt aus 100% gekämmter Baumwolle, 240 g/m² , figurbetont.</p>
        <p>Bitte wählen Sie Ihre Größe: Größe S - Größe M - Größe L - Größe XL</p>
      </div>
      <p class="order-number">Bestellnummer : <span>111 - 234567</span></p>
      <div class="shirt-image" role="img" aria-label="Produktfoto: schwarzes Damen-Shirt mit weißem Polospieler-Motiv und Städtenamen München"></div>
      <p class="price">25 €</p>
    </article>
  </section>
</main>
</body>
</html>
```